Dietary supplement, Clean and simple.

Hi,
I’d like to talk about the project,

About us:
We are a dietary supplement (Vitamins, Minerals, amino acids etc.) company.
The goal is to have about 25 products at the end of this year. However, for this goal to be achieved we need a good label design to make our products represent our company values.
I’ll be here every day supporting your questions, we are fully committed to making the highest/best quality/customer experience possible.

About the design and our values:
- Professional (We are in the industry of professionalism and expertise. I would love to show we are competent at this, Id. Like to have the labels looks like we have done our research.)
- Efficient (White spacing, good use of the space available.)
- Simple (Straight forward, in 5 seconds they have to know what the product they have is/how functions. We’re trying to simplify it for the consumer.
- No distractions (the only visually “distracting” factor can be the vector art.)

The guidelines:
The goal is to have a universal design, with one element that changes (Vector art). I’ll attach a file/multiple files I think can show some visuals on what I’m looking for, and what parts of the design I think are good/bad.

Label size: 69x155mm (Front is 77.5mm)

Design whatever you think fits our image. You’re the design expert, all I care about is that it fits our company standards/image.

Use this color/font.
Font: Sans Serif
Main company color is Mind green #237D62 (Use this color for something in the design.)

What I thought would be cool/might looks ugly, who knows:
1. The front of the label: Should have 1 vector art, preferably in the top right corner. (That looks good in multiple colors. The vector can have multiple areas to color, I would prefer 2 main colors in the vector art. The interchangeable colors are used for multiple kinds of products.)
2. Text/product information on the left. The text that will have to be displayed:
- Product name for instance “Magnesium + B6”
- Description for the product for instance “Magnesium with ginger taste”
- Company name or logo. (Add ® behind it. We are soon to be trademark registered.)
3. We need to show the "daily intake" amount on the front and also the amount in the complete bottle. For instance, “Daily intake 1 capsule, 60 capsules”.
• You don’t have to design the backside of the label. After I chose a design, I’d like to chat and give specific information on what areas need to be assigned where. (Too complex because of the law.)
Updates

Hi, Please make the deadline 31 days total. I want designers to have the time to design. And not be rushed to finish it.

I want to extend the deadline because i feel like a slightly more medical look would be interesting. Hope you can come up with something!!

Target Market(s)

Dietary supplement consumers

Industry/Entity Type

Dietary supplements

Font styles to use
Sans Serif

Colors

Designer to choose colors to be used in the design.

Requirements
Must have
• Trademark icon "®" has to be at the top right after the company logo(text of logo)/name.

```html
<!DOCTYPE html>
<html lang="en">
<head>
<meta charset="utf-8">
<title>Verdant Calm – Magnesium + B6 Labels</title>
<link rel="stylesheet" href="https://fonts.googleapis.com/css2?family=Archivo:wght@400;500;700;800&display=swap">
<style>
  :root {
    --page-bg: #ffffff;
    --label-light: #efefef;
    --label-mid: #d6d6d6;
    --brand-green: #176b2c;
    --ink: #3b3b3b;
    --ink-soft: #6a6a6a;
    --accent-red: #e0523a;
    --art-orange-a: #f0a27a;
    --art-orange-b: #f5c9a6;
    --art-violet-a: #a99be8;
    --art-violet-b: #a9cdee;
    --art-green-a: #8fc79a;
    --art-green-b: #d2efaa;
  }
  * { margin: 0; padding: 0; box-sizing: border-box; }
  html, body {
    width: 1200px;
    height: 873px;
    overflow: hidden;
    background: var(--page-bg);
    font-family: "Archivo", Arial, sans-serif;
  }
  .label-row {
    position: relative;
    width: 1200px;
    height: 873px;
  }
  .label {
    position: absolute;
    top: 236px;
    width: 340px;
    height: 400px;
    overflow: hidden;
    background:
      radial-gradient(ellipse 70% 60% at 35% 55%, var(--label-mid) 0%, rgba(214,214,214,0) 70%),
      linear-gradient(90deg, var(--label-mid) 0%, var(--label-light) 55%, #f6f6f6 100%);
  }
  .label--orange { left: 45px; }
  .label--violet { left: 430px; }
  .label--green  { left: 815px; }

  .brand {
    position: absolute;
    left: 36px;
    top: 70px;
    color: var(--brand-green);
    font-weight: 800;
  }
  .brand__name {
    display: block;
    font-size: 30px;
    line-height: 1;
    letter-spacing: -0.5px;
  }
  .brand__mark {
    font-size: 10px;
    vertical-align: top;
    margin-left: 2px;
  }
  .brand__sub {
    display: block;
    font-size: 11px;
    letter-spacing: 7px;
    margin-top: 4px;
    padding-left: 18px;
  }

  .art {
    position: absolute;
    right: 0;
    top: 30px;
    width: 110px;
    height: 120px;
  }
  .label--orange .art { background: linear-gradient(90deg, var(--art-orange-a), var(--art-orange-b)); }
  .label--violet .art { background: linear-gradient(90deg, var(--art-violet-a), var(--art-violet-b)); }
  .label--green  .art { background: linear-gradient(90deg, var(--art-green-a), var(--art-green-b)); }

  .product {
    position: absolute;
    left: 36px;
    top: 220px;
    color: var(--ink);
  }
  .product__name {
    font-size: 22px;
    font-weight: 700;
    line-height: 1;
  }
  .product__desc {
    font-size: 7.5px;
    letter-spacing: 1.8px;
    color: var(--ink-soft);
    margin-top: 5px;
    font-weight: 500;
  }

  .dosage {
    position: absolute;
    left: 36px;
    top: 270px;
    color: var(--ink);
  }
  .dosage__value {
    font-size: 14px;
    font-weight: 700;
    line-height: 1;
  }
  .dosage__value--large { font-size: 15px; }
  .dosage__unit {
    font-size: 6px;
    color: var(--ink-soft);
    margin-top: 1px;
  }
  .dosage__rule {
    width: 20px;
    height: 2px;
    background: var(--accent-red);
    margin: 10px 0 12px;
  }
</style>
</head>
<body>
<main class="label-row">

  <section class="label label--orange">
    <div class="brand">
      <span class="brand__name">VERDANT<span class="brand__mark">®</span></span>
      <span class="brand__sub">CALM</span>
    </div>
    <div class="art" role="img" aria-label="Placeholder for the product's orange and red colour artwork"></div>
    <div class="product">
      <h2 class="product__name">MAGNESIUM + B6</h2>
      <p class="product__desc">MAGNESIUM WITH GINGER TASTE</p>
    </div>
    <div class="dosage">
      <p class="dosage__value">60</p>
      <p class="dosage__unit">CAPSULES</p>
      <div class="dosage__rule"></div>
      <p class="dosage__value dosage__value--large">1 CAPSULE</p>
      <p class="dosage__unit">DAILY INTAKE</p>
    </div>
  </section>

  <section class="label label--violet">
    <div class="brand">
      <span class="brand__name">VERDANT<span class="brand__mark">®</span></span>
      <span class="brand__sub">CALM</span>
    </div>
    <div class="art" role="img" aria-label="Placeholder for the product's violet and blue colour artwork"></div>
    <div class="product">
      <h2 class="product__name">MAGNESIUM + B6</h2>
      <p class="product__desc">MAGNESIUM WITH GINGER TASTE</p>
    </div>
    <div class="dosage">
      <p class="dosage__value">60</p>
      <p class="dosage__unit">CAPSULES</p>
      <div class="dosage__rule"></div>
      <p class="dosage__value dosage__value--large">1 CAPSULE</p>
      <p class="dosage__unit">DAILY INTAKE</p>
    </div>
  </section>

  <section class="label label--green">
    <div class="brand">
      <span class="brand__name">VERDANT<span class="brand__mark">®</span></span>
      <span class="brand__sub">CALM</span>
    </div>
    <div class="art" role="img" aria-label="Placeholder for the product's green and lime colour artwork"></div>
    <div class="product">
      <h2 class="product__name">MAGNESIUM + B6</h2>
      <p class="product__desc">MAGNESIUM WITH GINGER TASTE</p>
    </div>
    <div class="dosage">
      <p class="dosage__value">60</p>
      <p class="dosage__unit">CAPSULES</p>
      <div class="dosage__rule"></div>
      <p class="dosage__value dosage__value--large">1 CAPSULE</p>
      <p class="dosage__unit">DAILY INTAKE</p>
    </div>
  </section>

</main>
</body>
</html>
```